Webdesign for large cottage directory

We have developed a first version of a website that can accommodate large groups (10 to 300 people). The site is English and is aimed at a wide audience ranging from a group of students to a family or a family. For the visitors the site is free and it is the propietaires who pay to see their accommodation. The site is online with just a few fake lodgings and a simple design to the elements that must be appraised (nothing to keep the current design). Our website is here: 9lodgia.com (login / pass = admin / 123) Home page (9lodgia.com): on this page section) and lodging by theme (third section). These three points should be highlighted as possible. The displayed map may be slightly modified. Only the background and the color changes when hovering over the mouse. It can be enlarged / retreciated. Below these 3 sections we have some fairly published articles, the latest blog posts and the footer. The menu will be visible throughout the site. Category page (https://9lodgia.fr/gite-departement/aveyron OR https://9lodgia.fr/gites-couchages-121): On these pages we always return the same format with the googlemap, an image 1 text. Below the list of the cottages concerned and the filter options. Product page: The pages presenting the cottages can be of two types: - Either the cottage has no owner and there is no contact for the visitor to the owner that he can retrieve his cottage by registering: example of a page of this type: https://9lodgia.fr/domaine-de-vercasse - The cottage to a propietaire and we are on the classic card. : // 9lodgia. en / domain-of-vercasse2 For all products on the site we have nav tab. It's just for testing. We do not want to be in the design for real website. All information must be in the page without login / register page: classic, it's here: https://9lodgia.it/login and https://9lodgia.fr/register Blog homepage (https://9lodgia.fr/blog ): Classic blog page Blog post (https://9lodgia.fr/blog/urltemporaire1551521154) and static page (https://9lodgia.fr/blog/Systeme-classement-9lodgiafr): Nothing special Menu: Menu is an important part of the website. It's the way to navigate on the wbesite.
Faible participation designers
4 page

```html
<!DOCTYPE html>
<html lang="en">
<head>
<meta charset="utf-8">
<title>9lodgia — Large cottage directory</title>
<link href="https://fonts.googleapis.com/css2?family=Montserrat:wght@400;500;600;700&family=Open+Sans:wght@400;600&family=Arimo:wght@400&display=swap" rel="stylesheet">
<style>
:root{
  --blue:#1457ff;
  --blue-dark:#0e46d6;
  --white:#ffffff;
  --ink:#3b3b3b;
  --muted:#555;
  --ring-grey:#a9a9a9;
  --map-bg:#cfe2c6;
  --map-land:#eeeeec;
  --ad-green:#0f8a6e;
}
*{margin:0;padding:0;box-sizing:border-box}
html,body{width:1200px;height:3120px;overflow:hidden;background:var(--white)}
body{position:relative;font-family:"Open Sans",Arial,sans-serif;color:var(--ink)}
.abs{position:absolute}

/* header */
.site-header{position:absolute;left:0;top:0;width:1200px;height:79px;background:var(--blue);border-bottom:2px solid var(--white)}
.brand{position:absolute;font-family:"Arimo",Arial,sans-serif;color:var(--white);font-size:31px;left:110px;top:20px}
.main-nav{position:absolute;left:380px;top:32px;display:flex;gap:0}
.main-nav a,.footer-nav a{font-family:"Montserrat",Arial,sans-serif;font-weight:600;font-size:13px;text-transform:uppercase;text-decoration:none;letter-spacing:.2px}
.main-nav a{color:var(--white);margin-right:43px}
.main-nav a:last-child{margin-right:0}

/* hero */
.hero{position:absolute;left:0;top:79px;width:1200px;height:607px;background:linear-gradient(180deg,#2a3350 0%,#4a3a38 45%,#2b2722 100%)}
.hero-title{position:absolute;left:0;width:1200px;top:240px;text-align:center;color:var(--white);font-family:"Montserrat",sans-serif;font-weight:400;font-size:86px;letter-spacing:1px}
.hero-text{position:absolute;left:0;width:1200px;top:352px;text-align:center;color:var(--white);font-size:18px;line-height:30px}
.hero-arrow{position:absolute;top:286px;width:36px;height:36px;border:2px solid var(--white);border-radius:50%}

/* sections */
.section-title{position:absolute;left:0;width:1200px;text-align:center;font-family:"Montserrat",sans-serif;font-weight:700;font-size:33px;color:var(--ink)}
.rule{position:absolute;left:556px;width:88px;height:4px;background:var(--blue)}
.capacity{position:absolute;width:160px;text-align:center}
.capacity-label{font-family:"Montserrat",sans-serif;font-weight:500;font-size:17px;line-height:26px;color:var(--ink);margin-top:4px}

.department{position:absolute;left:0;top:1088px;width:1200px;height:570px;background:var(--map-bg)}
.map{position:absolute;left:364px;top:78px;width:468px;height:510px}
.tooltip{position:absolute;left:467px;top:245px;background:#222;color:#fff;font-size:13px;font-weight:600;padding:3px 6px}

.theme-tile{position:absolute;width:314px;height:200px;display:flex;align-items:center;justify-content:center;color:var(--white);font-family:"Montserrat",sans-serif;font-weight:700;font-size:25px;text-transform:uppercase}
.theme-tile.brand-tile{background:var(--blue);font-family:"Arimo",Arial,sans-serif;font-weight:400;text-transform:none;font-size:33px}

/* ad */
.ad{position:absolute;left:193px;top:2469px;width:816px;height:100px;background:var(--ad-green);color:var(--white)}
.ad-photo{position:absolute;left:0;top:0;width:188px;height:100px;background:linear-gradient(90deg,#b9c9c2,#7fa99a)}
.ad-name{position:absolute;left:10px;top:8px;font-size:18px;font-weight:600;color:var(--white)}
.ad-head{position:absolute;left:206px;top:12px;font-size:33px;line-height:34px;font-weight:400}
.ad-line{position:absolute;left:408px;top:20px;width:2px;height:62px;background:rgba(255,255,255,.6)}
.ad-copy{position:absolute;left:440px;top:8px;font-size:15px;font-weight:600;line-height:20px;width:360px}
.ad-btn{position:absolute;left:440px;top:58px;background:var(--white);color:var(--ad-green);font-size:14px;font-weight:700;padding:5px 12px}
.ad-sponsor{position:absolute;right:12px;bottom:8px;font-size:13px;font-weight:600}

/* blog */
.blog{position:absolute;left:0;top:2627px;width:1200px;height:352px;background:var(--blue);color:var(--white)}
.blog .section-title{color:var(--white)}
.blog .rule{background:var(--white)}
.post-date{position:absolute;width:92px;height:92px;border:2px solid var(--white);border-radius:50%;text-align:center;font-family:"Montserrat",sans-serif}
.post-date b{display:block;font-weight:500;font-size:33px;margin-top:14px;line-height:36px}
.post-date span{font-size:18px}
.post{position:absolute;width:200px}
.post h3{font-family:"Montserrat",sans-serif;font-weight:700;font-size:17px;text-transform:uppercase;margin-bottom:12px}
.post p{font-size:12.5px;line-height:24px}
.post a{display:block;color:var(--white);font-size:12.5px;margin-top:10px}

/* footer */
.footer-brand{position:absolute;left:110px;top:3018px;font-family:"Arimo",Arial,sans-serif;color:var(--blue);font-size:44px}
.footer-nav{position:absolute;left:375px;top:3013px}
.footer-nav a{color:var(--ink);margin-right:39px}
.footer-nav a:last-child{margin-right:0}
.copyright{position:absolute;left:375px;top:3059px;font-size:13px;color:var(--muted)}
.social{position:absolute;top:3061px;width:22px;height:22px;border:1px solid #888;border-radius:50%}
</style>
</head>
<body>

<header class="site-header">
  <div class="brand">9lodgia.Fr</div>
  <nav class="main-nav">
    <a>Gîte par capacité</a><a>Gîte par département</a><a>Gîte par thématique</a><a>Blog</a><a>Vos favoris</a>
  </nav>
</header>

<section class="hero" role="img" aria-label="Wooden chalet at dusk among trees">
  <div class="hero-arrow" style="left:67px">
    <svg width="32" height="32" viewBox="0 0 32 32"><path d="M18 10l-6 6 6 6" fill="none" stroke="#fff" stroke-width="2"/></svg>
  </div>
  <div class="hero-arrow" style="left:1095px">
    <svg width="32" height="32" viewBox="0 0 32 32"><path d="M14 10l6 6-6 6" fill="none" stroke="#fff" stroke-width="2"/></svg>
  </div>
  <h1 class="hero-title">9lodgia</h1>
  <p class="hero-text">Sed ut perspiciatis unde omnis iste natus error sit voluptatem accusantium<br>doloremque laudantium, totam rem aperiam</p>
</section>

<h2 class="section-title" style="top:727px">LODGING BY CAPACITY</h2>
<div class="rule" style="top:778px"></div>

<svg class="abs" style="left:0;top:840px" width="1200" height="140" viewBox="0 0 1200 140">
  <defs>
    <g id="ring-base">
      <circle r="55" fill="none" stroke="var(--ring-grey)" stroke-width="14" pathLength="120" stroke-dasharray="9 1" transform="rotate(-90)"/>
    </g>
  </defs>
  <g font-family="Montserrat, sans-serif" font-size="27" fill="#555" text-anchor="middle">
    <g transform="translate(187,67)"><use href="#ring-base"/><circle r="55" fill="none" stroke="var(--blue)" stroke-width="14" pathLength="120" stroke-dasharray="9 1 9 1 9 91" transform="rotate(-90)"/><text y="9">1-20</text></g>
    <g transform="translate(354,67)"><use href="#ring-base"/><circle r="55" fill="none" stroke="var(--blue)" stroke-width="14" pathLength="120" stroke-dasharray="9 1 9 1 9 1 9 81" transform="rotate(-90)"/><text y="9">1-20</text></g>
    <g transform="translate(518,67)"><use href="#ring-base"/><circle r="55" fill="none" stroke="var(--blue)" stroke-width="14" pathLength="120" stroke-dasharray="9 1 9 1 9 1 9 1 9 71" transform="rotate(-90)"/><text y="9">1-20</text></g>
    <g transform="translate(684,67)"><use href="#ring-base"/><circle r="55" fill="none" stroke="var(--blue)" stroke-width="14" pathLength="120" stroke-dasharray="9 1 9 1 9 1 9 1 9 1 9 1 9 51" transform="rotate(-90)"/><text y="9">1-20</text></g>
    <g transform="translate(851,67)"><use href="#ring-base"/><circle r="55" fill="none" stroke="var(--blue)" stroke-width="14" pathLength="120" stroke-dasharray="9 1 9 1 9 1 9 1 9 1 9 1 9 1 9 1 9 31" transform="rotate(-90)"/><text y="9">1-20</text></g>
    <g transform="translate(1017,67)"><use href="#ring-base"/><circle r="55" fill="none" stroke="var(--blue)" stroke-width="14" pathLength="120" stroke-dasharray="9 1 9 1 9 1 9 1 9 1 9 1 9 1 9 1 9 1 9 1 9 11" transform="rotate(-90)"/><text y="9">1-20</text></g>
  </g>
</svg>
<div class="capacity" style="left:107px;top:976px"><div class="capacity-label">2 to 20<br>People</div></div>
<div class="capacity" style="left:274px;top:976px"><div class="capacity-label">20 to 40<br>People</div></div>
<div class="capacity" style="left:438px;top:976px"><div class="capacity-label">40 to 60<br>People</div></div>
<div class="capacity" style="left:604px;top:976px"><div class="capacity-label">60 to 80<br>People</div></div>
<div class="capacity" style="left:771px;top:976px"><div class="capacity-label">80 to 120<br>People</div></div>
<div class="capacity" style="left:937px;top:976px"><div class="capacity-label">more than<br>120 People</div></div>

<section class="department">
  <h2 class="section-title" style="top:32px">LODGING BY DEPARTMENT</h2>
  <div class="map" role="img" aria-label="Clickable map of France by department" style="background:radial-gradient(ellipse at 50% 45%,var(--map-land) 0%,var(--map-land) 55%,rgba(238,238,236,0) 72%)"></div>
  <div class="tooltip" style="left:467px;top:245px">Indre and Loire</div>
</section>

<h2 class="section-title" style="top:1698px">LODGING BY THEME</h2>
<div class="rule" style="top:1753px"></div>

<div class="theme-tile" style="left:112px;top:1782px;background:linear-gradient(180deg,#4a3a4a,#2a1f22)" role="img" aria-label="Seminar audience in a conference hall">Seminar</div>
<div class="theme-tile" style="left:443px;top:1782px;background:linear-gradient(180deg,#c9b37a,#6e6a45)" role="img" aria-label="Person with raised arms in a sunny field">Peach</div>
<div class="theme-tile" style="left:774px;top:1782px;background:linear-gradient(180deg,#5a8d96,#1e4f5c)" role="img" aria-label="Iceberg in turquoise water">Aquatic</div>
<div class="theme-tile" style="left:112px;top:1999px;background:linear-gradient(180deg,#7d7560,#4d4a3a)" role="img" aria-label="Rider on a horse in a paddock">Horse riding</div>
<div class="theme-tile brand-tile" style="left:443px;top:1999px">9lodgia.Fr</div>
<div class="theme-tile" style="left:774px;top:1999px;background:linear-gradient(180deg,#6d6a66,#a86a2e)" role="img" aria-label="Mountain biker at sunset">Mountain bike</div>
<div class="theme-tile" style="left:112px;top:2211px;background:linear-gradient(180deg,#7a4a2c,#3a2a1c)" role="img" aria-label="Grilled meat with vegetables">Gastronomic</div>
<div class="theme-tile" style="left:443px;top:2211px;background:linear-gradient(180deg,#3d4a2e,#6a4a28)" role="img" aria-label="Group of friends around a campfire">Summer camp</div>
<div class="theme-tile" style="left:774px;top:2211px;background:linear-gradient(180deg,#8d97a3,#4a4a44)" role="img" aria-label="Snowy mountain peaks">Snow nature &amp; hike</div>

<aside class="ad">
  <div class="ad-photo" role="img" aria-label="Business owner at work"></div>
  <div class="ad-name">Qwent</div>
  <div class="ad-head">Expand your<br>business</div>
  <div class="ad-line"></div>
  <div class="ad-copy">People are searching for a business like yours. Be found with Qwent Ads.</div>
  <div class="ad-btn">Try it now</div>
  <div class="ad-sponsor">Northvale</div>
</aside>

<section class="blog">
  <h2 class="section-title" style="top:28px">LATEST BLOG</h2>
  <div class="rule" style="top:81px"></div>

  <div class="post-date" style="left:112px;top:133px"><b>10</b><span>APR</span></div>
  <div class="post" style="left:225px;top:136px"><h3>Sed ut perspiciatis</h3><p>Sed ut perspiciatis unde omnis iste natus error sit voluptatem accusan-tium doloremque laudantium, totam error sit rem aperiam....</p><a>Read More</a></div>

  <div class="post-date" style="left:449px;top:133px"><b>15</b><span>APR</span></div>
  <div class="post" style="left:562px;top:136px"><h3>Sed ut perspiciatis</h3><p>Sed ut perspiciatis unde omnis iste natus error sit voluptatem accusan-tium doloremque laudantium, totam error sit rem aperiam....</p><a>Read More</a></div>

  <div class="post-date" style="left:786px;top:133px"><b>08</b><span>APR</span></div>
  <div class="post" style="left:899px;top:136px"><h3>Sed ut perspiciatis</h3><p>Sed ut perspiciatis unde omnis iste natus error sit voluptatem accusan-tium doloremque laudantium, totam error sit rem aperiam....</p><a>Read More</a></div>
</section>

<footer>
  <div class="footer-brand">9lodgia.Fr</div>
  <nav class="footer-nav">
    <a>Gîte par capacité</a><a>Gîte par département</a><a>Gîte par thématique</a><a>Blog</a><a>Vos favoris</a>
  </nav>
  <p class="copyright">© Copyright-2019 9 Lodgia. All rights reserved.</p>
  <span class="social" style="left:958px"></span>
  <span class="social" style="left:985px"></span>
  <span class="social" style="left:1012px"></span>
  <span class="social" style="left:1039px"></span>
  <span class="social" style="left:1066px"></span>
</footer>

</body>
</html>
```